Elegant Business Card for Technology Company

Client is a supplier of innovative industrial communications and automation equipment since 2002. This contest is to gather fresh ideas for a redesign of the existing business card. Client is looking for design that best communicates tagline "Industrial Networking and Computing Specialist".

Design submissions should look modern, clean, elegant and professional. It should not be cluttered. Use white as the primary colour. Orange and black as secondary colour. Refer to jpeg File 1 on the current design.

Fonts used by Client used include Arial Regular, Arial Black, Roboto Regular, Roboto Black and Lato.

The winning design will be sent for offset printing using super white 250gsm artcard paper (open for suggestions).

Target Market(s)

System Engineers, Project Managers, Purchasing Managers from companies providing engineering services for Smart Cities.

Industry/Entity Type

Information Technology

Contact Information for Business Card

Refer to PDF File 3 for Business Card Details. Priority of short contact information would be as follows Name > Job Title > Email > Mobile > Web > Tel > Fax > Business Address >UEN (UEN represents company registration number)

Font styles to use
Sans Serif

Colors
ffffff
f37122
000000
5c5c5c

Requirements
Must have
• Refer to AI File 2 (Company Logo) & PDF File 3 (Information on Namecard)
Should not have
• No QR codes
• No Social Media Icons
• Do not create full Black or Orange colour background

```html
<!DOCTYPE html>
<html lang="en">
<head>
<meta charset="utf-8">
<title>Norvex Business Card</title>
<link rel="stylesheet" href="https://fonts.googleapis.com/css2?family=Roboto:wght@400;500;700;900&display=swap">
<style>
  :root {
    --white: #ffffff;
    --orange: #f37122;
    --black: #000000;
    --ink: #1a1a1a;
    --grey: #5c5c5c;
    --rule: #d4d4d4;
    --stage: #e9e7e3;
  }
  * { box-sizing: border-box; margin: 0; padding: 0; }
  html, body { width: 1200px; height: 950px; overflow: hidden; }
  body {
    background: var(--stage);
    font-family: "Roboto", Arial, sans-serif;
    position: relative;
  }
  .card {
    position: absolute;
    left: 320px;
    width: 560px;
    height: 320px;
    border-radius: 22px;
    overflow: hidden;
    background: var(--white);
    box-shadow: 0 10px 28px rgba(0,0,0,0.18);
  }

  /* Front */
  .card-front { top: 110px; }
  .front-accent {
    position: absolute;
    left: 0; right: 0; bottom: 0;
    height: 14px;
    background: var(--orange);
  }
  .front-brand {
    position: absolute;
    left: 0; right: 0;
    top: 76px;
    text-align: center;
    font-weight: 900;
    font-size: 72px;
    line-height: 84px;
    letter-spacing: 2px;
    color: var(--orange);
  }
  .front-tagline {
    position: absolute;
    left: 0; right: 0;
    top: 186px;
    text-align: center;
    font-size: 14.5px;
    line-height: 20px;
    color: var(--grey);
  }

  /* Back */
  .card-back { top: 500px; }
  .back-swoosh { position: absolute; inset: 0; }
  .holder {
    position: absolute;
    right: 34px;
    top: 14px;
    text-align: right;
  }
  .holder-name {
    color: var(--orange);
    font-weight: 700;
    font-size: 18px;
  }
  .holder-title {
    color: var(--white);
    font-size: 12.5px;
    margin-top: 2px;
  }
  .divider {
    position: absolute;
    left: 300px;
    top: 108px;
    width: 1px;
    height: 190px;
    background: linear-gradient(var(--white), var(--rule) 30%, var(--rule) 70%, var(--white));
  }
  .contact {
    position: absolute;
    left: 322px;
    top: 112px;
    color: var(--grey);
    font-size: 13px;
    line-height: 18px;
  }
  .contact-address { margin-bottom: 2px; }
  .contact-list { list-style: none; }
  .contact-list li { display: flex; align-items: center; gap: 8px; height: 18px; }
  .contact-list svg { width: 12px; height: 12px; flex: none; fill: var(--orange); }
  .brand-name {
    position: absolute;
    left: 112px;
    top: 228px;
    font-weight: 900;
    font-size: 42px;
    line-height: 50px;
    color: var(--ink);
    letter-spacing: 1px;
  }
</style>
</head>
<body>

<section class="card card-front">
  <div class="front-brand">Norvex</div>
  <p class="front-tagline">
    Industrial Networking &amp; Computing Specialist<br>
    Industrial Ethernet / Wireless / Cellular<br>
    Industrial &amp; Embedded Computing / Serial / Fieldbus Connectivity<br>
    IP Video Surveillance / Remote Automation
  </p>
  <div class="front-accent"></div>
</section>

<section class="card card-back">
  <svg class="back-swoosh" viewBox="0 0 560 320" preserveAspectRatio="none">
    <path d="M0,0 H560 V62 C470,60 380,66 300,86 C190,112 90,150 0,250 Z" fill="#000000"/>
    <path d="M0,282 C70,180 160,128 300,96 C360,84 420,80 480,82 C400,88 330,100 280,114 C160,148 70,200 0,282 Z" fill="#f37122"/>
  </svg>

  <div class="holder">
    <div class="holder-name">Daniel Reyes</div>
    <div class="holder-title">Sales Manager</div>
  </div>

  <div class="divider"></div>

  <div class="contact">
    <p class="contact-address">22 Harbour Link<br>Unit #05-12 (Block B)<br>Singapore 409876</p>
    <ul class="contact-list">
      <li><svg viewBox="0 0 12 12"><path d="M2.5 1l2 2.2-1 1.3c.7 1.4 1.6 2.3 3 3l1.3-1 2.2 2-1.2 1.8C5 10 2 7 1 2.3z"/></svg>+65 6100 2040</li>
      <li><svg viewBox="0 0 12 12"><path d="M3.5 0h5a1 1 0 0 1 1 1v10a1 1 0 0 1-1 1h-5a1 1 0 0 1-1-1V1a1 1 0 0 1 1-1zm.5 1.5v7.5h4V1.5z"/></svg>+65 9100 3050</li>
      <li><svg viewBox="0 0 12 12"><path d="M3 0h5v3H3zM1 4h10v6H9v2H3v-2H1zm3 4v3h4V8z"/></svg>+65 6100 2041</li>
      <li><svg viewBox="0 0 12 12"><path d="M0 2h12v1.2L6 7 0 3.2zM0 4.6l6 3.8 6-3.8V10H0z"/></svg>sales@norvex.com.sg</li>
      <li><svg viewBox="0 0 12 12"><circle cx="6" cy="6" r="6"/><path d="M0 6h12M6 0c-2.5 3-2.5 9 0 12M6 0c2.5 3 2.5 9 0 12" stroke="#fff" stroke-width="0.8" fill="none"/></svg>www.norvex.com.sg</li>
    </ul>
  </div>

  <div class="brand-name">Norvex</div>
</section>

</body>
</html>
```